Bicycle Tour Schedule on a Business Card

Need to develop a 2 side business card that highlights a series of bike tours on 1 side and a series of events on the other side.
This will be inserted into a card wallet that attaches to a cell phone and will be handed out at an expo. The card wallets are black and red so color must coordinate with both. There is a photo of the card wallets attached.

1 side needs to be devoted to Pedal Vista Trek and the others to KQR Venture events on the other. Dates and websites are very important.

Target Market(s)

Cyclists
Predominantly men ages 40+
Educated, Professionals

Industry/Entity Type

Business

Font styles to use
Serif

Requirements
Must have
• Pedal vista treks logo on 1 side and KQR Venture logo on the other side
• dates and websites clearly visible
• Design of both sides must go together.
• Must be portrait not landscape

```html
<!DOCTYPE html>
<html lang="en">
<head>
<meta charset="utf-8">
<title>Pedal Vista Treks &amp; KQR Venture – Event Cards</title>
<link href="https://fonts.googleapis.com/css2?family=Open+Sans:ital,wght@0,400;0,700;1,700&display=swap" rel="stylesheet">
<style>
  :root {
    --bg: #e9e6e1;
    --white: #ffffff;
    --tour-blue: #1f64b4;
    --tour-blue-dark: #17529a;
    --tour-green: #4cb86a;
    --logo-blue: #1f5fae;
    --event-red: #d0112b;
    --event-red-dark: #b50d24;
    --event-teal: #1c95c3;
    --logo-red: #d0112b;
    --text-light: #ffffff;
  }
  * { box-sizing: border-box; margin: 0; padding: 0; }
  html, body { width: 1200px; height: 950px; overflow: hidden; }
  body {
    background: var(--bg);
    font-family: "Open Sans", Arial, sans-serif;
    position: relative;
  }
  .card {
    position: absolute;
    top: 125px;
    width: 400px;
    height: 700px;
    background: var(--white);
    border-radius: 6px;
    overflow: hidden;
    box-shadow: 0 6px 18px rgba(0,0,0,.18);
    display: flex;
    flex-direction: column;
    text-align: center;
    color: var(--text-light);
  }
  .card--tours { left: 150px; }
  .card--events { left: 650px; }

  .card__brand {
    height: 250px;
    display: flex;
    align-items: center;
    justify-content: center;
    gap: 14px;
  }
  .brand-name {
    font-weight: 700;
    font-size: 34px;
    line-height: 1.1;
  }
  .card--tours .brand-name { color: var(--logo-blue); }
  .card--events .brand-name { color: var(--logo-red); }
  .brand-dot {
    width: 34px; height: 34px; border-radius: 50%;
    background: var(--tour-green);
    flex: none;
  }
  .brand-square {
    width: 34px; height: 34px;
    background: var(--logo-red);
    flex: none;
  }

  .card__band {
    padding: 14px 26px;
    font-weight: 700;
    font-size: 21px;
    line-height: 1.3;
  }
  .card--tours .card__band { background: var(--tour-green); font-style: italic; }
  .card--events .card__band { background: var(--event-teal); }

  .card__body {
    flex: 1;
    padding: 34px 30px 30px;
  }
  .card--tours .card__body {
    background: linear-gradient(180deg, var(--tour-blue) 0%, var(--tour-blue-dark) 100%);
  }
  .card--events .card__body {
    background: linear-gradient(180deg, var(--event-red) 0%, var(--event-red-dark) 100%);
    padding-top: 22px;
  }

  .tour { margin-bottom: 22px; }
  .tour__name { font-size: 22px; font-weight: 400; line-height: 1.25; }
  .tour__date { font-size: 22px; font-weight: 700; line-height: 1.25; }

  .event { margin-bottom: 16px; line-height: 1.25; }
  .event__name { font-size: 20px; }
  .event__name--bold { font-weight: 700; }
  .event__date { font-size: 20px; }
  .event__date--bold { font-weight: 700; }
  .event__site { font-size: 20px; }
  .event__site--bold { font-weight: 700; }
</style>
</head>
<body>

  <section class="card card--tours" aria-label="Pedal Vista Treks tour schedule">
    <header class="card__brand">
      <span class="brand-dot" aria-hidden="true"></span>
      <span class="brand-name">Pedal Vista Treks</span>
    </header>
    <p class="card__band">Fully supported bike tours. Discover the hidden gems on two wheels</p>
    <div class="card__body">
      <div class="tour">
        <p class="tour__name">Heart of Colorado</p>
        <p class="tour__date">June 26 - July 2, 2016</p>
      </div>
      <div class="tour">
        <p class="tour__name">Colorado Front Range Tour</p>
        <p class="tour__date">August 14-20, 2016</p>
      </div>
      <div class="tour">
        <p class="tour__name">Cape Cod Tour</p>
        <p class="tour__date">October 9 -15, 2016</p>
      </div>
      <div class="tour">
        <p class="tour__name">Florida Key Tours</p>
        <p class="tour__date">November 6-12, 2016 &amp;<br>December 4-10, 2016</p>
      </div>
    </div>
  </section>

  <section class="card card--events" aria-label="KQR Venture event schedule">
    <header class="card__brand">
      <span class="brand-square" aria-hidden="true"></span>
      <span class="brand-name">KQR Venture</span>
    </header>
    <p class="card__band">Trio Wheel Series:<br>Cycling camps for youth</p>
    <div class="card__body">
      <div class="event">
        <p class="event__name">Mountain Bike Camp</p>
        <p class="event__date event__date--bold">July 8-10, 2016</p>
      </div>
      <div class="event">
        <p class="event__name">Cyclocross Camp</p>
        <p class="event__date event__date--bold">August 26-28, 2016</p>
        <p class="event__site event__site--bold">Triowheelseries.org</p>
      </div>
      <div class="event">
        <p class="event__name event__name--bold">Mile High Hundred Ride</p>
        <p class="event__date">June 18, 2016</p>
        <p class="event__site">Milehighhundred.com</p>
      </div>
      <div class="event">
        <p class="event__name event__name--bold">Front Range Loop Challenge</p>
        <p class="event__date">July 30, 2016</p>
        <p class="event__site">Frontrangeloop.com</p>
      </div>
      <div class="event">
        <p class="event__name event__name--bold">Zany Spoke Ride</p>
        <p class="event__date">September 11, 2016</p>
        <p class="event__site">zanyspokeride.com</p>
      </div>
    </div>
  </section>

</body>
</html>
```